Real Estate Card Design

I need a new business card! Below you will find my headshot, the company logo and a copy of my previous business card.

The card must contain the following information:

Dana Wexley
Sales Representative
HOLLISMERE HOMES REALTY INC BROKERGE
204-517 Marsh Rd E, Oshawa ON L1H 4K7
Cell: 905-618-3074 Office:905-481-2696
www.danawexley.example dana@homesbywexley.example

I would like the card to portray security and class all the while being fresh and contemporary. I hold the key....

```html
<!DOCTYPE html>
<html lang="en">
<head>
<meta charset="utf-8">
<title>Dana Wexley – Business Card</title>
<link rel="stylesheet" href="https://fonts.googleapis.com/css2?family=Libre+Bodoni:wght@700&family=Montserrat:wght@400;500;600&display=swap">
<style>
  :root {
    --backdrop: #2b2b2b;
    --card: #ffffff;
    --brand-blue: #27a3e3;
    --ink: #111111;
    --photo-dark: #121716;
    --photo-mid: #2a3230;
  }
  * { box-sizing: border-box; margin: 0; padding: 0; }
  html, body { width: 1200px; height: 895px; overflow: hidden; }
  body {
    background: var(--backdrop);
    font-family: "Montserrat", sans-serif;
    color: var(--ink);
  }
  .business-card {
    position: absolute;
    left: 100px; top: 162px;
    width: 1000px; height: 572px;
    background: var(--card);
    box-shadow: 0 14px 30px rgba(0,0,0,.45);
  }
  .brand {
    position: absolute;
    right: 60px; top: 62px;
    display: flex; align-items: center; gap: 14px;
  }
  .brand-square {
    width: 64px; height: 64px;
    background: var(--brand-blue);
    flex: none;
  }
  .brand-name {
    font-weight: 600;
    font-size: 17px;
    line-height: 1.25;
    letter-spacing: .04em;
    color: var(--ink);
    width: 220px;
  }
  .headshot {
    position: absolute;
    left: 62px; top: 196px;
    width: 262px; height: 262px;
    border: 2px solid var(--brand-blue);
  }
  .headshot-fill {
    position: absolute;
    left: 10px; top: 10px; right: 10px; bottom: 10px;
    background: radial-gradient(circle at 45% 40%, var(--photo-mid), var(--photo-dark) 70%);
  }
  .agent {
    position: absolute;
    left: 350px; top: 200px;
  }
  .agent-name {
    font-family: "Libre Bodoni", serif;
    font-weight: 700;
    font-size: 36px;
    letter-spacing: .03em;
    color: var(--brand-blue);
    text-transform: uppercase;
    line-height: 1;
  }
  .agent-title {
    font-size: 18px;
    font-weight: 500;
    margin-top: 4px;
  }
  .contact {
    position: absolute;
    left: 596px; top: 322px;
    list-style: none;
    font-size: 19px;
    line-height: 1.45;
    white-space: nowrap;
  }
  .contact-label { color: var(--brand-blue); }
  .address {
    position: absolute;
    left: 62px; top: 482px;
    font-size: 20px;
    line-height: 1.35;
    font-style: normal;
  }
  .accent-band {
    position: absolute;
    right: 0; bottom: 0;
    width: 315px; height: 16px;
    background: var(--brand-blue);
  }
</style>
</head>
<body>
  <article class="business-card">
    <div class="brand">
      <span class="brand-square"></span>
      <span class="brand-name">HOLLISMERE HOMES REALTY INC BROKERGE</span>
    </div>

    <div class="headshot">
      <div class="headshot-fill" role="img" aria-label="Headshot of Dana Wexley holding a key"></div>
    </div>

    <div class="agent">
      <h1 class="agent-name">Dana Wexley</h1>
      <p class="agent-title">Sales Representative</p>
    </div>

    <ul class="contact">
      <li><span class="contact-label">Cell:</span> 905-618-3074</li>
      <li><span class="contact-label">Office:</span> 905-481-2696</li>
      <li><span class="contact-label">Email:</span> dana@homesbywexley.example</li>
      <li><span class="contact-label">Web:</span> www.danawexley.example</li>
    </ul>

    <address class="address">204-517 Marsh Rd E<br>Oshawa ON L1H 4K7</address>

    <div class="accent-band"></div>
  </article>
</body>
</html>
```